Logo and Website Design for QR.KA Horizon - a Software Engineering and IT company

Software engineering and IT are two different disciplines - and yet inseparably linked. At QR.KA Horizon, we combine both worlds and ensure that our software solutions are not only innovative and powerful, but also integrate perfectly into existing IT landscapes. Vision stands more for imagination, so it is not neccessary something what has to do with visualisation. Please consider that the winning competitor is also instructed to make a logo for the company. So please make a suitable logo for QR.KA Horizon to which the website fits to and show it during the website creation process. A good Logo desing is important for winning the competition. The website should contain a landing page with inspiring, perhaps futuristic photos of a datacenter and lines of code. Eventuelly flewent integrated in the text. On the landing page the company should introduced with a small text (max 250 words) followed by a section with a short text to one of our products nearby a graphic visualising the architecture of the product. The menue should be on top and fixed during scrolling and consist of the menue items home, solutions, who are we and a contact button. There should be a footer for linking social media, rights and Impressum. Only as an idea not a must. The very first view on the landing page could also be the menue bar and below of it a transparent unsharp photo (e.g. datacenter, lines of code, both ;) with the company name in the center.

###############################################################

Hi Designers,

Despite your very good approaches for describing QR.KA Horizon, here a short introduction (german text) from ourself:

------
QR.KA Horizon – Ihr Partner für ganzheitliche Softwarelösungen

Die QR.KA Horizon ist ein dynamisches Unternehmen, das sich nicht nur auf die Konzeption, das Design und die Entwicklung maßgeschneiderter Software spezialisiert hat, sondern auch deren reibungslosen Betrieb sicherstellt. Mit einem Team aus erfahrenen Softwarearchitekten und IT-Professionals verbinden wir modernste Softwareentwicklung mit tiefgehendem IT-Know-how – für Lösungen, die nachhaltig, leistungsstark und zukunftssicher sind.

Software Engineering trifft IT – Perfektion in Kombination
Software Engineering und IT sind zwei unterschiedliche Disziplinen – und doch untrennbar miteinander verbunden. Wir bei QR.KA Horizon vereinen beide Welten und sorgen dafür, dass unsere Softwarelösungen nicht nur innovativ und leistungsfähig sind, sondern sich auch perfekt in bestehende IT-Landschaften integrieren.

Expertise mit Fokus auf Healthcare & komplexe IT-Umgebungen
Unsere Experten bringen jahrzehntelange Erfahrung aus dem Healthcare-Sektor mit und unterstützen IT-Abteilungen großer Kliniken in der Entwicklung und Optimierung von Softwarelösungen. Von Anwendungssoftware bis hin zu Steuerungssystemen – unsere Softwareingenieure wissen genau, worauf es ankommt.

Ganzheitlicher Ansatz – über die Software hinaus
Wir entwickeln nicht nur Software, sondern übernehmen auch die Verantwortung für deren stabile und effiziente Betriebsumgebung. Egal, ob on-premises, in der Cloud oder als SaaS-Lösung – wir kümmern uns um den kompletten Lifecycle Ihrer Anwendung.

Ihre Vision – unsere Mission.
Ob Neuentwicklung einer SaaS-Anwendung oder die Migration bestehender Lösungen in eine moderne SaaS-Umgebung – mit QR.KA Horizon haben Sie einen starken Partner an Ihrer Seite.

Lassen Sie uns gemeinsam die Zukunft Ihrer Software gestalten!
--------------

Our first solution called "Clear Record Transfer Gateway" (CLURA)
-------------------
Teilen Sie Ihre Daten sicher – ohne Kompromisse!

Sie nutzen eine relationale Datenbank (Brightcask, Tabulon Hub, Vellumdb etc.) und möchten ausgewählte Daten mit Dritten teilen – sei es für ein Data Warehouse, Business Controller, Lieferanten oder Kunden? Doch dabei sollen Datensicherheit, Integrität und Verfügbarkeit Ihrer primären Lösung in keiner Weise gefährdet werden?

Mit unserer Lösung erhalten Sie genau das: Maximalen Schutz für Ihre Anwendung bei gleichzeitigem Nutzen durch autorisierte Dritte – ganz ohne teure Lizenzkosten für eine Schattendatenbank.

Lassen Sie uns gemeinsam herausfinden, wie Sie Ihre Daten sicher und effizient nutzen können. Kontaktieren Sie uns – wir zeigen Ihnen, was möglich ist!
---------------------

Our second solution MIVO:
---------------------
MIVO – Program for a Tone Matching Instrument ist die smarte Lösung für Unternehmen, die bei Farbgenauigkeit keine Kompromisse machen. Die Software erkennt Farbabweichungen zwischen Mustern vollautomatisch, beschreibt sie verständlich und sorgt so für gleichbleibend hohe Produktqualität – schnell, visuell und präzise. Perfekt für alle, die Farbe zur Vertrauenssache machen.
-------------------------

Thanks,
Gerold

Target Market(s)

IT Professionals from any sector

Industry/Entity Type

Healthcare and other

Coding

Coded - Design and coding required

Number of Pages Required

1 page

Font styles to use
Sans Serif

Colors
0054AA
0677BA
7BADD7
CADEEF
E8F1F8
0094D4
00A9DD
6FCCEA
C7EBF8
E9F6FB
00AB8E
00BBA5
67D7C9
C6EFE9
E9F9F6

Requirements
Must have
• Please see description
Nice to have
• On the landing page the company should introduced with a small text (max 250 words) followed by a section with a short text to one of our products nearby a graphic visualising the architecture of the product. The menue should be on top and fixed during scrolling and consist of the menue items home, solutions, who are we and a contact button. There should be a footer for linking social media, rights and Impressum. Only as an idea not a must. The very first view on the landing page could also be the menue bar and below of it a transparent unsharp photo (e.g. datacenter, lines of code, both ;) with the company name in the center.
Should not have
• Please see description

```html
<!DOCTYPE html>
<html lang="en">
<head>
<meta charset="utf-8">
<title>QR.KA Horizon</title>
<link href="https://fonts.googleapis.com/css2?family=Lato:wght@400;700&display=swap" rel="stylesheet">
<style>
:root{
  --blue:#1e9fd4;
  --blue-deep:#0677ba;
  --ink:#1b1b1b;
  --text:#3a3a3a;
  --muted:#5a5a5a;
  --white:#ffffff;
  --soft:#f0f0f0;
  --card:#fbfaf7;
  --dark:#1d1d1f;
  --star:#f28c0f;
}
*{margin:0;padding:0;box-sizing:border-box}
html,body{width:1200px;height:3737px;overflow:hidden}
body{font-family:'Lato',sans-serif;color:var(--text);background:var(--white);position:relative}
.abs{position:absolute}
a{color:inherit;text-decoration:none}

/* hero */
.hero{left:0;top:0;width:1200px;height:740px}
.hero-photo{position:absolute;inset:0;background:linear-gradient(180deg,#10202c 0%,#1d3a4c 45%,#0f1c26 100%)}
.hero-shade{position:absolute;inset:0;background:rgba(10,20,30,.35)}
.hero-curve{position:absolute;left:0;top:600px}
.nav{left:112px;top:28px;width:976px;height:60px;display:flex;align-items:center}
.brand{display:flex;align-items:center;gap:10px;color:var(--white);font-weight:700;font-size:36px;letter-spacing:-.5px}
.brand-dot{width:48px;height:48px;border:4px solid var(--white);border-radius:50%}
.menu{margin-left:auto;display:flex;align-items:center;gap:40px;color:var(--white);font-size:15px}
.menu .active{background:var(--blue);padding:7px 9px}
.btn{display:inline-block;background:var(--blue);color:var(--white);font-weight:700;font-size:15px}
.menu .btn{padding:11px 28px;margin-left:0}
.hero-title{left:0;width:1200px;top:168px;text-align:center;color:var(--white);font-weight:700;font-size:78px;letter-spacing:-1px}
.hero-sub{left:0;width:1200px;top:274px;text-align:center;color:var(--white);font-size:22px;line-height:32px}
.hero-cta{left:494px;top:363px;width:206px;height:40px;line-height:40px;text-align:center;font-size:15px}
.dots{left:565px;top:671px;display:flex;gap:9px}
.dots span{width:11px;height:11px;border-radius:50%;background:rgba(255,255,255,.5)}
.dots span:first-child{background:var(--white)}

h2.section-title{font-size:44px;font-weight:700;color:var(--ink);letter-spacing:-.5px}
h2.section-title em{font-style:normal;color:var(--blue)}

/* products */
.products-title{left:0;width:1200px;top:810px;text-align:center}
.arrow{width:34px;height:34px;border-radius:50%;background:var(--blue);top:975px}
.product{top:892px;width:309px}
.product-img{height:190px;border-radius:3px}
.product-head{display:flex;align-items:center;gap:22px;margin-top:26px;font-size:21px;color:var(--ink)}
.product-icon{width:44px;height:44px;background:var(--blue);border-radius:4px}
.product p{margin-top:22px;font-size:14.5px;line-height:22px}
.product .rule{height:2px;background:var(--blue-deep);margin-top:24px}

/* about */
.about{left:0;top:1355px;width:1200px;height:667px}
.about-text{left:645px;top:1448px;width:445px;color:var(--white)}
.about-text h2{font-size:44px;font-weight:700;margin-bottom:22px}
.about-text p{font-size:14.5px;line-height:25.7px;margin-bottom:20px}
.dark-btn{display:inline-block;background:#222;color:var(--white);font-weight:700;font-size:15px;padding:12px 35px;margin-top:16px}

/* testimonials */
.testimonials{left:0;top:2022px;width:1200px;height:440px;background:var(--soft)}
.testimonials-title{left:0;width:1200px;top:2095px;text-align:center}
.quote{top:2190px;width:317px;height:228px;background:var(--card);border:1px solid #e4e4e4;border-radius:3px;padding:26px 23px}
.quote.featured{background:var(--blue);border-color:var(--blue);color:var(--white)}
.stars{color:var(--star);font-size:16px;letter-spacing:1px}
.quote.featured .stars{color:var(--white)}
.quote p{margin-top:16px;font-size:14.5px;line-height:22px;color:var(--muted)}
.quote.featured p,.quote.featured .who,.quote.featured .date{color:var(--white)}
.who{margin-top:18px;font-size:17px;color:var(--ink)}
.date{margin-top:10px;font-size:13px;color:var(--muted)}
.t-dots{left:577px;top:2442px;display:flex;gap:4px}
.t-dots span{width:13px;height:5px;border-radius:3px;background:#c6c6c6}
.t-dots span:first-child{background:var(--blue)}

/* solutions */
.solutions-text{left:112px;top:2648px;width:440px}
.solutions-text h4{margin-top:22px;color:var(--blue);font-size:17px;font-weight:700}
.solutions-text p{margin-top:22px;font-size:14.5px;line-height:25.7px}
.solutions-text .btn{margin-top:38px;padding:12px 36px}
.solutions-visual{left:650px;top:2630px}

/* footer */
.footer{left:0;top:3150px;width:1200px;height:587px}
.footer-brand{left:0;width:1200px;top:3240px;display:flex;justify-content:center;align-items:center;gap:14px;color:var(--white);font-size:50px;font-weight:700;letter-spacing:-.5px}
.footer-brand .mark{width:62px;height:62px;background:var(--blue);border-radius:50%}
.f-col{top:3380px;color:var(--white)}
.f-col h3{font-size:21px;font-weight:700;margin-bottom:28px}
.f-col p,.f-col li{font-size:14.5px;line-height:25.7px}
.f-col ul{list-style:none}
.f-col ul li{margin-bottom:21px;line-height:26px}
.contact li{display:flex;gap:22px;align-items:flex-start;margin-bottom:22px}
.contact svg{flex:none;margin-top:3px}
.social{left:112px;top:3565px;display:flex;gap:18px;align-items:center}
.social .s{width:28px;height:28px;border:2px solid var(--white);border-radius:6px}
.social .s.on{width:40px;height:40px;background:var(--blue);border-color:var(--blue)}
.f-rule{left:112px;top:3702px;width:976px;height:1px;background:#3a3a3c}
.copyright{left:0;width:1200px;top:3713px;text-align:center;color:var(--white);font-size:13px}
</style>
</head>
<body>

<!-- Hero -->
<section class="abs hero">
  <div class="hero-photo" role="img" aria-label="Blurred data center with engineers at monitors showing lines of code"></div>
  <div class="hero-shade"></div>
  <svg class="hero-curve" width="1200" height="140" viewBox="0 0 1200 140">
    <path d="M0 30 Q600 190 1200 30 L1200 140 L0 140 Z" fill="#fff"/>
    <path d="M90 45 Q600 180 1110 45 Q600 150 90 45 Z" fill="var(--blue)"/>
  </svg>
  <div class="dots abs"><span></span><span></span><span></span><span></span></div>
</section>

<header class="abs nav">
  <div class="brand"><span class="brand-dot"></span>QR.KA Horizon</div>
  <nav class="menu">
    <a class="active" href="#">Home</a>
    <a href="#">Solutions</a>
    <a href="#">Who Are We</a>
    <a href="#">Contact</a>
    <a class="btn" href="#">Get Started</a>
  </nav>
</header>
<h1 class="abs hero-title">QR.KA HORIZON</h1>
<p class="abs hero-sub">Bridging the gap between software engineering and IT to<br>create powerful, future-ready solutions.</p>
<a class="abs btn hero-cta" href="#">Schedule a Consultation</a>

<!-- Products -->
<h2 class="abs section-title products-title">Our <em>Products</em></h2>
<svg class="abs arrow" style="left:58px" viewBox="0 0 34 34"><circle cx="17" cy="17" r="17" fill="var(--blue)"/><path d="M20 10 L13 17 L20 24" stroke="#fff" stroke-width="3" fill="none"/></svg>
<svg class="abs arrow" style="left:1108px" viewBox="0 0 34 34"><circle cx="17" cy="17" r="17" fill="var(--blue)"/><path d="M14 10 L21 17 L14 24" stroke="#fff" stroke-width="3" fill="none"/></svg>

<article class="abs product" style="left:112px">
  <div class="product-img" role="img" aria-label="Glowing cloud above a circuit board" style="background:linear-gradient(135deg,#0a3550,#1e7fb0 55%,#0a2a40)"></div>
  <div class="product-head"><span class="product-icon"></span>QR.KA CloudSync</div>
  <p>A seamless cloud integration tool that ensures real-time data synchronization between on-premise and cloud environments.</p>
  <div class="rule"></div>
</article>
<article class="abs product" style="left:446px">
  <div class="product-img" role="img" aria-label="Glass infinity loop on a processor chip" style="background:linear-gradient(135deg,#0c2c4a,#2a7fb8 55%,#0c2740)"></div>
  <div class="product-head"><span class="product-icon"></span>QR.KA SecureOps</div>
  <p>A security and operations automation platform for monitoring, compliance, and threat detection.</p>
  <div class="rule" style="width:145px"></div>
</article>
<article class="abs product" style="left:780px">
  <div class="product-img" role="img" aria-label="Light bulb glowing with AI circuitry" style="background:linear-gradient(135deg,#1d3f56,#4a7f9c 50%,#18354a)"></div>
  <div class="product-head"><span class="product-icon"></span>QR.KA AI Assist</div>
  <p>Designing and implementing digital transformation initiatives, including agile methodologies and DevOps practices.</p>
  <div class="rule" style="width:153px"></div>
</article>

<!-- About -->
<section class="abs about">
  <svg width="1200" height="667" viewBox="0 0 1200 667">
    <defs>
      <linearGradient id="aboutBg" x1="0" y1="0" x2="1" y2="0">
        <stop offset="0" stop-color="#0b2a45"/><stop offset=".45" stop-color="#1b6d9e"/><stop offset="1" stop-color="#2098cf"/>
      </linearGradient>
    </defs>
    <path d="M0 105 Q600 -70 1200 105 L1200 667 L0 667 Z" fill="url(#aboutBg)"/>
    <path d="M90 80 Q600 -60 1110 80 Q600 -30 90 80 Z" fill="var(--blue)"/>
  </svg>
  <div class="abs" role="img" aria-label="Glowing translucent cubes over a circuit board" style="left:0;top:110px;width:620px;height:557px;background:radial-gradient(ellipse at 45% 45%,rgba(120,200,255,.45),rgba(10,40,70,0) 70%)"></div>
</section>
<div class="abs about-text">
  <h2>About Us</h2>
  <p>At QR.KA Horizon, we bridge the gap between software engineering and IT, creating innovative and seamlessly integrated solutions. Our expertise ensures that businesses benefit from software that is powerful, scalable, and adaptable to existing IT landscapes. We believe in the power of imagination and technology—not just developing software, but crafting future-ready solutions that drive efficiency, security, and automation.</p>
  <p>Our approach combines cutting-edge engineering with a deep understanding of IT infrastructure, allowing organizations to innovate without disruption. In today's fast-paced digital landscape, businesses require software that is not only innovative but also compatible with their evolving IT environments. That's where we come in.</p>
  <a class="dark-btn" href="#">Read More</a>
</div>

<!-- Testimonials -->
<section class="abs testimonials"></section>
<svg class="abs" style="left:0;top:2430px" width="1200" height="120" viewBox="0 0 1200 120">
  <path d="M0 0 L1200 0 L1200 10 Q600 120 0 10 Z" fill="var(--soft)"/>
  <path d="M90 35 Q600 135 1110 35 Q600 110 90 35 Z" fill="var(--blue)"/>
</svg>
<h2 class="abs section-title testimonials-title">Our <em>Testimonials</em></h2>
<div class="abs quote" style="left:112px">
  <div class="stars">★★★★★</div>
  <p>Excepteur sint occaecat cupidatat non proident, sunt in culpa qui officia deserunt mollit anim id est laborum.</p>
  <div class="who">Halvorsen</div><div class="date">Apr 04 2025</div>
</div>
<div class="abs quote featured" style="left:441px">
  <div class="stars">★★★★★</div>
  <p>Excepteur sint occaecat cupidatat non proident, sunt in culpa qui officia deserunt mollit anim id est laborum.</p>
  <div class="who">Nadia</div><div class="date">Apr 04 2025</div>
</div>
<div class="abs quote" style="left:771px">
  <div class="stars">★★★★★</div>
  <p>Excepteur sint occaecat cupidatat non proident, sunt in culpa qui officia deserunt mollit anim id est laborum.</p>
  <div class="who">Corinne</div><div class="date">Apr 04 2025</div>
</div>
<div class="abs t-dots"><span></span><span></span><span></span></div>

<!-- Solutions -->
<div class="abs solutions-text">
  <h2 class="section-title">Our <em>Solutions</em></h2>
  <h4>Smart Solutions for Seamless IT Integration</h4>
  <p>At QR.KA Horizon, we develop cutting-edge solutions that bridge the gap between software engineering and IT. Our products are designed to be scalable, secure, and effortlessly integrated, empowering businesses with automation, efficiency, and innovation. Our expertise in software engineering and IT enables us to create scalable, secure, and high-performance solutions tailored to enterprise needs.</p>
  <a class="btn" href="#">Read More</a>
</div>
<svg class="abs solutions-visual" width="440" height="440" viewBox="0 0 440 440" role="img" aria-label="Glowing wrench and screwdriver on a blue circuit board">
  <defs>
    <radialGradient id="solBg" cx=".5" cy=".45" r=".6">
      <stop offset="0" stop-color="#2a6d98"/><stop offset="1" stop-color="#0b2a45"/>
    </radialGradient>
  </defs>
  <path d="M225 5 A215 215 0 1 0 225 435" fill="none" stroke="var(--blue)" stroke-width="4"/>
  <circle cx="229" cy="220" r="213" fill="url(#solBg)"/>
</svg>

<!-- Footer -->
<svg class="abs footer" width="1200" height="587" viewBox="0 0 1200 587">
  <path d="M0 110 Q600 -60 1200 110 L1200 587 L0 587 Z" fill="var(--dark)"/>
  <path d="M100 85 Q600 -50 1100 85 Q600 -20 100 85 Z" fill="var(--blue)"/>
</svg>
<div class="abs footer-brand"><span class="mark"></span>QR.KA HORIZON</div>

<div class="abs f-col" style="left:112px;width:300px">
  <h3>Our Mission</h3>
  <p>Our mission is to seamlessly connect these worlds, delivering software solutions that are powerful, scalable, and effortlessly integrated into existing IT infrastructures.</p>
</div>
<div class="abs f-col" style="left:483px">
  <h3>Main Links</h3>
  <ul><li>Home</li><li>Solutions</li><li>Who We Are</li><li>Contact</li></ul>
</div>
<div class="abs f-col" style="left:680px;width:240px">
  <h3>Contact Us</h3>
  <ul class="contact">
    <li><svg width="18" height="22" viewBox="0 0 18 22"><path d="M9 21 C4 14 2 11 2 8 A7 7 0 0 1 16 8 C16 11 14 14 9 21 Z" fill="none" stroke="#fff" stroke-width="1.5"/><circle cx="9" cy="8" r="2.5" fill="none" stroke="#fff" stroke-width="1.5"/></svg><span>47 Meridian Lane, Suite 8, Harbor Point 20931</span></li>
    <li><svg width="18" height="18" viewBox="0 0 18 18"><path d="M3 1 L7 1 L8 5 L6 7 Q8 11 11 12 L13 10 L17 11 L17 15 Q17 17 15 17 Q1 15 1 3 Q1 1 3 1 Z" fill="none" stroke="#fff" stroke-width="1.4"/></svg><span>+ 1 555 014 2290</span></li>
    <li><svg width="18" height="14" viewBox="0 0 18 14"><rect x="1" y="1" width="16" height="12" fill="none" stroke="#fff" stroke-width="1.4"/><path d="M1 1 L9 8 L17 1" fill="none" stroke="#fff" stroke-width="1.4"/></svg><span>info@qrkahorizon.example</span></li>
  </ul>
</div>
<div class="abs f-col" style="left:981px">
  <h3>Other Links</h3>
  <ul><li>Testimonials</li><li>Privacy Policy</li><li>Terms of Use</li><li>Impressum</li></ul>
</div>

<div class="abs social" aria-label="Social media links">
  <span class="s on"></span><span class="s"></span><span class="s"></span><span class="s"></span>
</div>
<div class="abs f-rule"></div>
<p class="abs copyright">Copyright © 2025 QR.KA Horizon. All rights reserved.</p>

</body>
</html>
```